Creative, fresh business card design for Ripplecraft Facades

We need a fresh, creative business card design for Ripplecraft Facades. We are the manufacturer of Ripplecraft Facades in Australia. Wall panels are 2400 x 1200mm panels made from MDF and feature 3D patterns on the face of the panel. The colours to be used are green, silver/grey and white RGB
Red 187
Green 207
Blue 65.

An idea is to possibly use a watermark of one of our designs as a background (like on the "Grids" design on the left hand side of page 2 of our brochure).

Target Market(s)

Interior designers, architects, builders and home renovators

Industry/Entity Type

Business

Contact Information for Business Card

Details to go on the card are:
Our logo (attached),
Slogan: "Decorative panels for interiors and exteriors",
Contact name,
Position,
Mobile phone number,
Business address,
Business phone,
Business fax,
Website and
Email address.

I have attached a few images of our panels and our brochure for reference.

The colours of the business card should feature our logo colours which are: RGB
Red 187
Green 207
Blue 65

Requirements
Must have
• Very modern fonts and design. Some of the designs shown especially the "Prisms" design which is a popular design.
Nice to have
• Creative but simple design. Very contemporary.
Should not have
• Anything ornate or old fashioned.

```html
<!DOCTYPE html>
<html lang="en">
<head>
<meta charset="utf-8">
<title>Ripplecraft Facades – Business Card</title>
<link rel="stylesheet" href="https://fonts.googleapis.com/css2?family=Oswald:wght@600&family=Titillium+Web:wght@400;600&display=swap">
<style>
  :root {
    --stage: #2a2a2a;
    --card: #1b1b1c;
    --lime: #bbcf41;
    --white: #f2f2f2;
    --silver: #a9a9ab;
  }
  * { margin: 0; padding: 0; box-sizing: border-box; }
  html, body { width: 1200px; height: 1000px; overflow: hidden; }
  body {
    background: var(--stage);
    font-family: "Titillium Web", sans-serif;
    position: relative;
  }
  .card {
    position: absolute;
    left: 160px; top: 247px;
    width: 880px; height: 506px;
    background: var(--card);
    border-radius: 36px;
    box-shadow: 0 20px 50px rgba(0,0,0,.5);
  }
  .brand {
    position: absolute;
    left: 470px; top: 92px;
    display: flex; align-items: center; gap: 16px;
  }
  .brand-mark { width: 58px; height: 58px; background: var(--lime); }
  .brand-name {
    font-weight: 600; font-size: 30px; line-height: 1;
    color: var(--silver);
  }
  .brand-tagline {
    font-size: 15px; letter-spacing: 1px; color: var(--silver);
    margin-top: 6px; line-height: 1.1;
  }
  .divider {
    position: absolute;
    left: 210px; top: 282px;
    width: 640px; height: 3px;
    background: var(--lime);
  }
  .person { position: absolute; left: 212px; top: 196px; }
  .person-name {
    font-family: "Oswald", sans-serif; font-weight: 600;
    font-size: 42px; line-height: 1; color: var(--lime);
    text-transform: uppercase; letter-spacing: 1px;
  }
  .person-role { font-size: 24px; color: var(--white); line-height: 1.3; }
  .phones { position: absolute; left: 215px; top: 300px; list-style: none; }
  .phones li, .contact li {
    display: flex; align-items: center; gap: 14px;
    font-size: 21px; color: var(--white); height: 30px;
  }
  .phones li { padding-left: 0; }
  .phones li:nth-child(2) { padding-left: 12px; }
  .phones li:nth-child(3) { padding-left: 24px; }
  .contact {
    position: absolute; right: 30px; top: 298px; list-style: none;
    text-align: right;
  }
  .contact li { justify-content: flex-end; }
  .contact .accent { color: var(--lime); }
  .icon { width: 18px; height: 18px; fill: var(--lime); flex: none; }
  .icon-gap { width: 18px; flex: none; }
</style>
</head>
<body>
  <section class="card">
    <div class="brand">
      <span class="brand-mark"></span>
      <div>
        <div class="brand-name">Ripplecraft Facades</div>
        <div class="brand-tagline">decorative panels for<br>interiors &amp; landscapes</div>
      </div>
    </div>

    <div class="person">
      <div class="person-name">Alden Marsh</div>
      <div class="person-role">Director</div>
    </div>

    <div class="divider"></div>

    <ul class="phones">
      <li><svg class="icon" viewBox="0 0 18 18"><rect x="5" y="1" width="8" height="16" rx="1.5"/><rect x="6.5" y="3" width="5" height="10" fill="#1b1b1c"/></svg>+000 123 456 789</li>
      <li><svg class="icon" viewBox="0 0 18 18"><path d="M4 2l3 3-1.5 2a9 9 0 0 0 5.5 5.5L13 11l3 3-2 2C7 15 3 11 2 4z"/></svg>+000 123 456 789</li>
      <li><svg class="icon" viewBox="0 0 18 18"><rect x="5" y="2" width="8" height="5"/><rect x="2" y="7" width="14" height="7" rx="1"/><rect x="5" y="11" width="8" height="5"/></svg>+000 123 456 789</li>
    </ul>

    <ul class="contact">
      <li>yourname@email.com<svg class="icon" viewBox="0 0 18 18"><rect x="1" y="4" width="16" height="11"/><path d="M1 4l8 6 8-6" stroke="#1b1b1c" stroke-width="1.5" fill="none"/></svg></li>
      <li><span>www.<span class="accent">websitename</span>.com</span><svg class="icon" viewBox="0 0 18 18"><circle cx="10" cy="7" r="5" fill="none" stroke="#bbcf41" stroke-width="2.5"/><path d="M7 10l-5 6" stroke="#bbcf41" stroke-width="3"/></svg></li>
      <li>Your Street Address, New York, 1234<span class="icon-gap"></span></li>
    </ul>
  </section>
</body>
</html>
```